Web Site Design for a Finance (lending) Company

We are opening a new subsidiary that focuses on lending money in the real estate industry. We need a web site designed to represent the business.

The business is lending money to real estate investors. A typical client/borrower will be looking to borrow money to buy a house, renovate it and then sell it at a profit, all within 12 months or less.

Company name is RTV Finance. Our logo is attached.

Attached is a general outline for the web site. We're working on writing more text for each page but this should give you enough to get started with some ideas.

Competitor web site that I like a lot (as an example): https://dorvaleqcapital.example/. Many of the general items on this site match what we will need (description of loan programs, FAQ)

Target Market(s)

Real estate investors (generally individuals or small companies with just a few people) who are buying homes, renovating them and then selling them at a profit.

Industry/Entity Type

Finance

Coding

Coded - Design and coding required

Number of Pages Required

5+ page

Colors

Designer to choose colors to be used in the design.

Requirements
Must have
• Minimalist design. Clean lines without too much clutter. Some stock photography is ok but the photos should not be distracting. They should almost fade in to the background so that user can focus on the key information about what our company does instead. We are a finance company, not a design company, so the information about our products will be more interesting to site visitors than the art.
• Some minimalist examples from Snapboard:
• https://www.snapboardia.example/explore/minimalist-web-design/
Nice to have
• If you search in zoovle for "hard money lenders" you will find many examples of web sites from our competition. I have provided a link above to competitor web site that I like a lot.
• I have attached our logo in EPS format. Logo is green. Web site doesn't have to be green but it should be of a color that will work well with the logo.

```html
<!DOCTYPE html>
<html lang="en">
<head>
<meta charset="utf-8">
<title>RTV Finance</title>
<link href="https://fonts.googleapis.com/css2?family=Lato:wght@400;700;900&family=Open+Sans:wght@400;600;700&display=swap" rel="stylesheet">
<style>
:root{
  --green:#0d5a36;
  --green-dark:#08432a;
  --green-wash:#2f6b45;
  --ink:#1d1d1d;
  --text:#6b6b6b;
  --line:#d9d9d9;
  --footer:#262626;
  --white:#ffffff;
}
*{box-sizing:border-box;margin:0;padding:0}
html,body{width:1200px;height:2985px;overflow:hidden;background:var(--white)}
body{position:relative;font-family:'Open Sans',Arial,sans-serif;color:var(--text)}
.abs{position:absolute}
.topbar{left:0;top:0;width:1200px;height:5px;background:var(--green)}
.brand{left:100px;top:20px;display:flex;align-items:center;gap:12px}
.brand-mark{width:22px;height:22px;background:var(--green)}
.brand-name{font-family:'Lato',sans-serif;font-weight:700;font-size:30px;color:var(--green)}
.phone{left:818px;top:24px;display:flex;align-items:center;gap:10px;font-size:13px;color:#333}
.apply{left:994px;top:22px;width:108px;height:34px;border:1px solid #bbb;border-radius:17px;font-size:12px;font-weight:600;color:#222;display:flex;align-items:center;justify-content:center}
.nav{top:78px;font-family:'Lato',sans-serif;font-size:16px;color:#222;font-weight:700}
.hero{left:0;top:114px;width:1200px;height:630px}
.hero-photo{position:absolute;inset:0;background:linear-gradient(100deg,#8a7a6a 0%,#d8d3cc 35%,#e9e6e1 60%,#c9c0a8 100%)}
.hero-title{left:0;width:1200px;top:368px;text-align:center;font-family:'Lato',sans-serif;font-weight:900;font-size:54px;color:var(--white);letter-spacing:2px}
.hero-sub{left:0;width:1200px;top:450px;text-align:center;font-size:22px;line-height:36px;color:var(--white);letter-spacing:1px}
.btn{display:flex;align-items:center;justify-content:center;gap:6px;border-radius:24px;font-family:'Lato',sans-serif;font-weight:700;font-size:14px}
.btn-hero{left:520px;top:548px;width:162px;height:48px;border:2px solid var(--white);color:var(--white)}
.btn-line{border:1.5px solid #aaa;color:#222;height:40px;background:var(--white)}
.arrow{width:32px;height:32px;border-radius:50%;background:rgba(0,0,0,.35);top:408px;display:flex;align-items:center;justify-content:center}
.h2{left:0;width:1200px;text-align:center;font-family:'Lato',sans-serif;font-weight:700;font-size:30px;color:var(--ink)}
.lead{left:270px;width:660px;text-align:center;font-size:12px;line-height:25px}
.card-photo{top:1076px;width:476px;height:282px;border:6px solid #f1f1f1}
.card-label{top:1326px;width:270px;height:46px;background:var(--white);display:flex;align-items:center;justify-content:center;font-family:'Lato',sans-serif;font-size:18px;color:var(--ink)}
.card-text{top:1416px;width:420px;text-align:center;font-size:12px;line-height:24px}
.why{left:0;top:1650px;width:1200px;height:450px;background:linear-gradient(180deg,#3d7a55,#2c6242)}
.why-col{top:1840px;width:240px;text-align:center;color:var(--white)}
.why-col h3{font-family:'Lato',sans-serif;font-weight:700;font-size:17px;margin:14px 0 14px}
.why-col p{font-size:12px;line-height:24px}
.partner{top:2320px;width:186px;height:120px;background:var(--white);box-shadow:0 0 0 1px #ececec;display:flex;align-items:center;justify-content:center;gap:8px;font-family:'Open Sans',sans-serif;font-weight:700;font-size:15px;color:#222}
.partner i{width:14px;height:14px;background:#222;display:block}
.dots{left:574px;top:2474px;display:flex;gap:8px}
.dots span{width:13px;height:13px;border-radius:50%;border:1.5px solid var(--green)}
.dots span:first-child{background:var(--green)}
.footer{left:0;top:2510px;width:1200px;height:475px;background:var(--footer)}
.fcol{top:2672px;color:var(--white)}
.fcol h4{font-family:'Lato',sans-serif;font-weight:700;font-size:16px;margin-bottom:42px}
.fcol ul{list-style:none;font-size:12px;line-height:31px}
.fcol li::before{content:"›";font-weight:700;margin-right:10px}
.contact-row{display:flex;gap:18px;font-size:12px;line-height:22px;margin-bottom:18px}
.email-box{width:276px;height:38px;border:1px solid #bbb;font-size:12px;padding:0 12px;display:flex;align-items:center;margin-top:22px}
.subscribe{margin-top:14px;width:112px;height:34px;border-radius:17px;background:var(--green);font-weight:700;font-size:13px;display:flex;align-items:center;justify-content:center}
.rule{left:100px;top:2904px;width:1004px;height:1px;background:#555}
.copy{left:100px;top:2944px;font-size:12px;color:var(--white)}
.social{left:760px;top:2934px;display:flex;gap:16px;font-size:12px;color:var(--white);align-items:center}
.social span{display:flex;align-items:center;gap:6px}
.social i{width:14px;height:14px;border:1.5px solid var(--white);border-radius:50%;display:block}
</style>
</head>
<body>
<div class="abs topbar"></div>

<header>
  <div class="abs brand"><span class="brand-mark"></span><span class="brand-name">RTV Finance</span></div>
  <div class="abs phone">
    <svg width="26" height="26" viewBox="0 0 26 26"><circle cx="13" cy="13" r="12" fill="none" stroke="#0d5a36" stroke-width="2"/><path d="M9 8c0 5 4 9 9 9l1-2-3-1-1 1c-2-1-3-2-4-4l1-1-1-3z" fill="#0d5a36"/></svg>
    <span>(+1) 123 456 7890</span>
  </div>
  <div class="abs apply">APPLY NOW</div>
  <svg class="abs" style="left:596px;top:56px" width="48" height="14" viewBox="0 0 48 14"><path d="M0 14L30 0 48 14z" fill="#0d5a36"/></svg>
  <nav>
    <span class="abs nav" style="left:596px">HOME</span>
    <span class="abs nav" style="left:680px">ABOUT US</span>
    <span class="abs nav" style="left:794px">LOANS</span>
    <span class="abs nav" style="left:882px">RESOURCES</span>
    <span class="abs nav" style="left:1010px">CONTACT US</span>
  </nav>
</header>

<section class="abs hero">
  <div class="hero-photo" role="img" aria-label="Photo of a couple meeting an advisor on a sofa in a bright living room"></div>
  <svg style="position:absolute;left:0;bottom:0" width="1200" height="110" viewBox="0 0 1200 110">
    <path d="M0 42L600 0 1200 42V110H0z" fill="#0d5a36"/>
    <path d="M0 60L600 110 1200 60V110H0z" fill="#ffffff"/>
  </svg>
</section>
<div class="abs arrow" style="left:28px;top:408px"><svg width="10" height="12"><path d="M8 1L2 6l6 5" stroke="#fff" stroke-width="2" fill="none"/></svg></div>
<div class="abs arrow" style="left:1140px;top:408px"><svg width="10" height="12"><path d="M2 1l6 5-6 5" stroke="#fff" stroke-width="2" fill="none"/></svg></div>
<h1 class="abs hero-title">RTV FINANCE</h1>
<p class="abs hero-sub">Local real estate experts lending to local<br>real estate investors</p>
<div class="abs btn btn-hero">LEARN MORE</div>

<section>
  <h2 class="abs h2" style="top:782px">WELCOME TO RTV FINANCE</h2>
  <p class="abs lead" style="top:846px">RTV Finance is a local business with local knowledge and strong industry relationships. A partner with a wide network who offers value added services. RTV has an established pool of experienced investors available for your real estate investment needs</p>
  <div class="abs btn btn-line" style="left:528px;top:954px;width:146px">READ MORE <svg width="14" height="14"><circle cx="7" cy="7" r="7" fill="#222"/><path d="M5 4l3 3-3 3" stroke="#fff" stroke-width="1.6" fill="none"/></svg></div>
</section>

<section>
  <div class="abs card-photo" style="left:100px;background:linear-gradient(180deg,#7fb6e6 0%,#c9d5dc 50%,#5f8a3c 100%)" role="img" aria-label="Photo of a large two-storey suburban house"></div>
  <div class="abs card-label" style="left:208px">FIX AND FLIP LOANS</div>
  <p class="abs card-text" style="left:128px">To take a trivial example, which of us ever undertakes laborious physical exercise, except to obtain some advantage from it? But who has any right to find fault with a man who chooses to enjoy</p>
  <div class="abs btn btn-line" style="left:256px;top:1512px;width:164px">LEARN MORE <svg width="14" height="14"><circle cx="7" cy="7" r="7" fill="#222"/><path d="M5 4l3 3-3 3" stroke="#fff" stroke-width="1.6" fill="none"/></svg></div>

  <div class="abs card-photo" style="left:626px;background:linear-gradient(160deg,#2a2a2a 0%,#4a4a4a 45%,#d9d6cf 100%)" role="img" aria-label="Photo of hands signing a loan contract beside cash and a calculator"></div>
  <div class="abs card-label" style="left:734px">COMMERCIAL LOANS</div>
  <p class="abs card-text" style="left:654px">To take a trivial example, which of us ever undertakes laborious physical exercise, except to obtain some advantage from it? But who has any right to find fault with a man who chooses to enjoy</p>
  <div class="abs btn btn-line" style="left:782px;top:1512px;width:164px">LEARN MORE <svg width="14" height="14"><circle cx="7" cy="7" r="7" fill="#222"/><path d="M5 4l3 3-3 3" stroke="#fff" stroke-width="1.6" fill="none"/></svg></div>
</section>

<section>
  <div class="abs why" role="img" aria-label="Green-tinted photo of an elegant living room interior"></div>
  <h2 class="abs h2" style="top:1730px;color:#fff">WHY BORROW FROM RTV</h2>
  <div class="abs why-col" style="left:86px">
    <svg width="46" height="44" viewBox="0 0 46 44"><circle cx="23" cy="10" r="7" fill="#fff"/><circle cx="9" cy="16" r="5" fill="#fff"/><circle cx="37" cy="16" r="5" fill="#fff"/><path d="M10 44c0-10 6-16 13-16s13 6 13 16z" fill="#fff"/><path d="M0 42c0-8 4-12 9-12 2 0 4 1 5 2-3 3-4 6-4 10z" fill="#fff"/><path d="M46 42c0-8-4-12-9-12-2 0-4 1-5 2 3 3 4 6 4 10z" fill="#fff"/></svg>
    <h3>EXPERTS</h3><p>Duis aute irure dolor in voluptate velit esse cillum dolore eu fugiat nulla pariatur. Excepteur cupidatat</p>
  </div>
  <div class="abs why-col" style="left:342px">
    <svg width="46" height="44" viewBox="0 0 46 44"><rect x="10" y="2" width="24" height="34" rx="2" fill="none" stroke="#fff" stroke-width="2.5"/><text x="22" y="24" fill="#fff" font-size="16" font-weight="700" text-anchor="middle" font-family="Open Sans">$</text><circle cx="34" cy="34" r="8" fill="#fff"/><path d="M30 34l3 3 5-6" stroke="#2f6b45" stroke-width="2" fill="none"/></svg>
    <h3>FAST APPROVAL</h3><p>Duis aute irure dolor in voluptate velit esse cillum dolore eu fugiat nulla pariatur. Excepteur cupidatat</p>
  </div>
  <div class="abs why-col" style="left:598px">
    <svg width="46" height="44" viewBox="0 0 46 44"><circle cx="16" cy="9" r="8" fill="#fff"/><path d="M2 44c0-14 6-22 14-22 5 0 8 2 10 6v16z" fill="#fff"/><rect x="26" y="28" width="18" height="14" rx="2" fill="#fff"/><rect x="32" y="25" width="6" height="4" fill="none" stroke="#fff" stroke-width="2"/></svg>
    <h3>PROFESSIONAL</h3><p>Duis aute irure dolor in voluptate velit esse cillum dolore eu fugiat nulla pariatur. Excepteur cupidatat</p>
  </div>
  <div class="abs why-col" style="left:880px">
    <svg width="56" height="44" viewBox="0 0 56 44"><path d="M0 12l10-4 8 16-8 4z" fill="#fff"/><path d="M56 12l-10-4-8 16 8 4z" fill="#fff"/><path d="M14 12l10-4h10l8 4-6 12-4-2-6 6-5-2-4 2z" fill="#fff"/></svg>
    <h3>A PARTNER</h3><p>Duis aute irure dolor in voluptate velit esse cillum dolore eu fugiat nulla pariatur. Excepteur cupidatat</p>
  </div>
</section>

<section>
  <h2 class="abs h2" style="top:2196px">OUR PARTNERS</h2>
  <p class="abs lead" style="top:2256px;left:200px;width:800px">Our management service organization is delegated and partnered with following Finance &amp; Real Estate</p>
  <div class="abs partner" style="left:100px"><i></i>Homestead Realty</div>
  <div class="abs partner" style="left:304px"><i></i>Winterhold</div>
  <div class="abs partner" style="left:510px"><i></i>Norvel Financial</div>
  <div class="abs partner" style="left:716px"><i></i>Keystone Group</div>
  <div class="abs partner" style="left:920px"><i></i>Orbis Lending</div>
  <div class="abs dots"><span></span><span></span><span></span></div>
</section>

<footer>
  <div class="abs footer"></div>
  <svg class="abs" style="left:0;top:2510px" width="1200" height="100" viewBox="0 0 1200 100">
    <path d="M0 0H1200L600 90z" fill="#0d5a36"/>
    <path d="M0 0H1200L600 72z" fill="#ffffff"/>
  </svg>
  <div class="abs fcol" style="left:100px">
    <h4>CONTACT US</h4>
    <div class="contact-row"><svg width="14" height="20"><path d="M7 19C2 12 1 9 1 7a6 6 0 0112 0c0 2-1 5-6 12z" fill="none" stroke="#fff" stroke-width="1.5"/><circle cx="7" cy="7" r="2" fill="#fff"/></svg><span>Old Simple Street, Old City,<br>New State</span></div>
    <div class="contact-row"><svg width="14" height="16"><path d="M2 2c0 7 5 12 11 12l1-3-3-1-2 1c-2-1-3-3-4-5l1-2-1-3z" fill="none" stroke="#fff" stroke-width="1.5"/></svg><span>(+1) 123 456 7890</span></div>
    <div class="contact-row"><svg width="16" height="14"><rect x="1" y="2" width="14" height="10" fill="none" stroke="#fff" stroke-width="1.5"/><path d="M1 2l7 6 7-6" fill="none" stroke="#fff" stroke-width="1.5"/></svg><span style="font-weight:700">info@rtvfinance.example</span></div>
  </div>
  <div class="abs fcol" style="left:386px">
    <h4>QUICK LIMNKS</h4>
    <ul><li>Home</li><li>About Us</li><li>Loans</li><li>Resources</li></ul>
  </div>
  <div class="abs fcol" style="left:596px">
    <h4>OTHER LINKS</h4>
    <ul><li>Contact us</li><li>Book A Callback</li><li>FAQs</li><li>Terms &amp; Conditions</li></ul>
  </div>
  <div class="abs fcol" style="left:830px">
    <h4>JOIN OUR NEWSLETTER</h4>
    <p style="font-size:12px;line-height:22px;margin-top:-18px;width:290px">Register your Email Address to get Information about us</p>
    <div class="email-box">Email Address</div>
    <div class="subscribe">SUBSCRIBE</div>
  </div>
  <div class="abs rule"></div>
  <p class="abs copy">© Copyright 2017 RTV Finance. All Rights Reserved</p>
  <div class="abs social"><span><i></i>Friendbook</span><span><i></i>Chirper</span><span><i></i>Snapboard</span><span><i></i>Pixgram</span></div>
</footer>
</body>
</html>
```